Report Design

I am looking for a redesign of our monthly inspection reports we submit to our customers. I uploaded the current one we use (FernHollows) and also that of a competitor (Tall Ridge). I want to more copy the layout of the Tallridge report I attached but with more flow and design.

Requirements
Must have
• This has to be in a template format that we can modify the content every month.

```html
<!DOCTYPE html>
<html lang="en">
<head>
<meta charset="utf-8">
<title>Landscape, Irr. &amp; Property Inspection</title>
<link href="https://fonts.googleapis.com/css2?family=Signika:wght@300;400;600;700&display=swap" rel="stylesheet">
<style>
  :root {
    --green-dark: #006b35;
    --green-bright: #4cc449;
    --green-text: #1f7a3e;
    --ink: #1a1a1a;
    --body: #2b2b2b;
    --paper: #ffffff;
  }
  * { box-sizing: border-box; margin: 0; padding: 0; }
  html, body { width: 848px; height: 1200px; overflow: hidden; background: var(--paper); }
  body { position: relative; font-family: "Signika", sans-serif; color: var(--body); }

  .report-title {
    position: absolute; left: 49px; top: 52px;
    font-size: 25px; font-weight: 600; color: var(--ink); letter-spacing: -0.2px;
  }
  .property-bar {
    position: absolute; left: 50px; top: 93px; width: 688px; height: 54px;
    background: var(--green-dark); color: #fff;
    font-size: 25px; font-weight: 600; padding-left: 13px; line-height: 54px;
  }
  .page-number {
    position: absolute; left: 753px; top: 93px; width: 51px; height: 54px;
    background: var(--green-bright); color: #fff;
    font-size: 25px; font-weight: 600; text-align: center; line-height: 54px;
  }
  .finding {
    position: absolute; left: 50px; width: 753px;
    border: 1.5px solid var(--green-dark);
  }
  .finding-1 { top: 169px; height: 425px; }
  .finding-2 { top: 613px; height: 443px; }
  .finding-heading {
    position: absolute; left: 22px; top: 24px;
    font-size: 18px; font-weight: 600; color: var(--green-dark);
  }
  .finding-heading .num { display: inline-block; width: 27px; }
  .finding-note {
    position: absolute; left: 22px; width: 712px;
    font-size: 15px; font-weight: 300; line-height: 19px; color: var(--body);
  }
  .finding-1 .finding-note { top: 56px; }
  .finding-2 .finding-note { top: 53px; }
  .site-photo { position: absolute; width: 339px; height: 291px; }
  .finding-1 .site-photo { top: 103px; }
  .photo-a { left: 22px; background: linear-gradient(180deg, #e9eced 0%, #8fa892 45%, #3e5b3a 70%, #6d6f70 100%); }
  .photo-b { left: 388px; background: linear-gradient(180deg, #e1e4e6 0%, #c7cbcd 35%, #5f7a4f 62%, #7a7c7e 85%, #b6b8b9 100%); }
  .photo-c { left: 22px; top: 119px; background: linear-gradient(180deg, #b7bcb4 0%, #7d8479 20%, #436336 45%, #4b3a32 80%, #a8a8a6 100%); }

  .footer-rule { position: absolute; left: 49px; top: 1080px; width: 756px; height: 1.5px; background: var(--green-dark); }
  .footer-title {
    position: absolute; left: 61px; top: 1098px;
    font-size: 21px; font-weight: 600; color: var(--ink);
  }
  .footer-division {
    position: absolute; left: 61px; top: 1127px;
    font-size: 15px; font-weight: 300; color: var(--green-text);
  }
  .footer-contacts {
    position: absolute; left: 62px; top: 1155px;
    display: flex; gap: 22px; font-size: 13.5px; font-weight: 300; color: var(--body);
  }
  .contact { display: flex; align-items: center; gap: 7px; }
  .contact svg { width: 14px; height: 14px; }
  .brand {
    position: absolute; left: 662px; top: 1120px; width: 140px; text-align: center;
  }
  .brand-name { font-size: 23px; font-weight: 700; color: var(--ink); display: flex; align-items: center; justify-content: center; gap: 6px; }
  .brand-name .mark { width: 11px; height: 11px; background: var(--green-dark); }
  .brand-tag { font-size: 8.5px; font-weight: 400; color: var(--ink); margin-top: 1px; }
</style>
</head>
<body>
  <h1 class="report-title">Landscape, Irr. &amp; Property Inspection</h1>
  <div class="property-bar">Gardens on Linden Park POA &amp; Retail</div>
  <div class="page-number">2</div>

  <section class="finding finding-1">
    <h2 class="finding-heading"><span class="num">3.</span>Palms Need Trimming:</h2>
    <p class="finding-note">All the Palms could use a trimming, there are dead frons and some hanging seed pods and boots. Let us know if and when you would like to get this scheduled.</p>
    <div class="site-photo photo-a" role="img" aria-label="Row of date palms along a median with shrub beds and a road"></div>
    <div class="site-photo photo-b" role="img" aria-label="Cluster of palms beside a crosswalk near a retail parking lot"></div>
  </section>

  <section class="finding finding-2">
    <h2 class="finding-heading"><span class="num">4.</span>Fill In:</h2>
    <p class="finding-note">We should fill this corner in where truck run over the corner with additional plants.</p>
    <div class="site-photo photo-c" role="img" aria-label="Curbed planting bed corner with thinned shrubs beside a road"></div>
  </section>

  <div class="footer-rule"></div>
  <div class="footer-title">Landscape, Irr. &amp; Property Inspection</div>
  <div class="footer-division">Landscape and Grounds Maintenance Division</div>
  <div class="footer-contacts">
    <span class="contact">
      <svg viewBox="0 0 16 16" aria-hidden="true"><circle cx="8" cy="8" r="8" fill="#1a1a1a"/><path d="M5.2 4.2l1.3-.3.8 1.8-.9.7c.5 1 1.2 1.7 2.2 2.2l.7-.9 1.8.8-.3 1.3c-2.9.2-5.8-2.7-5.6-5.6z" fill="#fff"/></svg>
      555-214-0187
    </span>
    <span class="contact">
      <svg viewBox="0 0 16 16" aria-hidden="true"><circle cx="8" cy="8" r="8" fill="#1a1a1a"/><rect x="5" y="6" width="6" height="5" fill="#fff"/><rect x="6" y="4" width="4" height="2" fill="#fff"/></svg>
      Fax 555-830-2291
    </span>
    <span class="contact">
      <svg viewBox="0 0 16 16" aria-hidden="true"><circle cx="8" cy="8" r="8" fill="#1a1a1a"/><path d="M8 3.5a2.6 2.6 0 0 0-2.6 2.6C5.4 8 8 11 8 11s2.6-3 2.6-4.9A2.6 2.6 0 0 0 8 3.5z" fill="#fff"/><circle cx="8" cy="6.1" r="1" fill="#1a1a1a"/><rect x="5" y="11.6" width="6" height="1" fill="#fff"/></svg>
      1200 Orchard Lane, Cedar Vale, FL 30000
    </span>
  </div>
  <div class="brand">
    <div class="brand-name"><span class="mark"></span>FernHollows</div>
    <div class="brand-tag">Landscape and Maintenance, Inc.</div>
  </div>
</body>
</html>
```